Professional, modern and unique business card. We are looking to present a new look to our business cards however we don't want to divert too far away from original template. We want social media links and our 3 office addresses on the backside of the business cards. Please see attached business card templates for ideas.
Crestline Homes Color Code:
R: 7
G:63
B:86

Target Market(s)

Real Estate

Industry/Entity Type

Real Estate

Contact Information for Business Card

Follow the attached templates. In need of a more modern and unique touch but don't want to divert from the original theme or color.
Crestline Homes Color Code:
R: 7
G:63
B:86

Font styles to use
Serif

Requirements
Must have
• Crestline Homes logo, Crestline homes colors, social media links, 3 office addresses,
Nice to have
• information about Crestline Homes and QR codes. You can check out www.mycrestlinehomes.example

```html
<!DOCTYPE html>
<html lang="en">
<head>
<meta charset="utf-8">
<title>Crestline Homes – Business Card</title>
<link href="https://fonts.googleapis.com/css2?family=Cinzel:wght@700&family=Lato:wght@400;700&display=swap" rel="stylesheet">
<style>
  :root {
    --stage: #161616;
    --card: #262626;
    --card-edge: #2e2e2e;
    --text: #f2f2f2;
    --rule: #5c5c5c;
    --brand: #073f56;
    --brand-light: #cde4ec;
    --accent-name: #9fcbdc;
    --icon-bg: #3a6f86;
  }
  * { margin: 0; padding: 0; box-sizing: border-box; }
  html, body { width: 1200px; height: 900px; overflow: hidden; }
  body {
    background: var(--stage);
    font-family: "Lato", Arial, sans-serif;
    color: var(--text);
    position: relative;
  }
  .card {
    position: absolute;
    width: 630px;
    height: 360px;
    background: var(--card);
    border: 1px solid var(--card-edge);
    border-radius: 22px;
    box-shadow: 0 20px 40px rgba(0,0,0,.6);
  }
  .card--back { left: 110px; top: 50px; }
  .card--front { left: 460px; top: 480px; }

  /* back side */
  .social { position: absolute; list-style: none; }
  .social li { display: flex; align-items: center; gap: 8px; font-size: 15px; margin-bottom: 9px; white-space: nowrap; }
  .social .badge {
    width: 20px; height: 20px; border-radius: 50%; flex: none;
    background: var(--icon-bg); display: flex; align-items: center; justify-content: center;
  }
  .social .badge svg { width: 12px; height: 12px; fill: none; stroke: var(--text); stroke-width: 1.8; stroke-linecap: round; }
  .social--left { left: 48px; top: 150px; }
  .social--right { left: 380px; top: 36px; }
  .back-rule { position: absolute; left: 40px; right: 40px; top: 255px; height: 1px; background: var(--rule); }
  .offices { position: absolute; left: 40px; right: 40px; top: 272px; display: flex; }
  .office { flex: 1; font-size: 15px; line-height: 1.3; padding: 0 12px; border-left: 1px solid var(--rule); white-space: nowrap; }
  .office:first-child { border-left: none; padding-left: 6px; }

  /* front side */
  .brand {
    position: absolute; right: 44px; top: 80px;
    display: flex; align-items: center; gap: 12px;
  }
  .brand__mark { width: 22px; height: 22px; border-radius: 50%; background: var(--brand-light); flex: none; }
  .brand__name { font-weight: 700; font-size: 32px; color: var(--brand-light); line-height: 1; white-space: nowrap; }
  .front-rule { position: absolute; left: 210px; right: 40px; top: 180px; height: 1px; background: var(--rule); }
  .person { position: absolute; left: 40px; top: 200px; }
  .person__name {
    font-family: "Cinzel", Georgia, serif; font-weight: 700;
    font-size: 21px; color: var(--accent-name); letter-spacing: .5px;
  }
  .person__title { font-size: 16px; margin-top: 2px; }
  .phones { list-style: none; position: absolute; left: 40px; top: 268px; }
  .phones li { display: flex; align-items: center; gap: 8px; font-size: 16px; line-height: 1.35; }
  .online { list-style: none; position: absolute; right: 40px; top: 200px; text-align: right; }
  .online li { display: flex; align-items: center; justify-content: flex-end; gap: 7px; font-size: 15px; line-height: 1.45; }
  .icon { width: 14px; height: 14px; fill: var(--text); flex: none; }
</style>
</head>
<body>

<section class="card card--back" aria-label="Card back">
  <ul class="social social--right">
    <li><span class="badge"><svg viewBox="0 0 12 12"><path d="M5 7l2-2M4 5.5L2.8 6.7a1.7 1.7 0 0 0 2.5 2.5L6.5 8M8 6.5l1.2-1.2a1.7 1.7 0 0 0-2.5-2.5L5.5 4"/></svg></span>Crestline Homes</li>
    <li><span class="badge"><svg viewBox="0 0 12 12"><path d="M5 7l2-2M4 5.5L2.8 6.7a1.7 1.7 0 0 0 2.5 2.5L6.5 8M8 6.5l1.2-1.2a1.7 1.7 0 0 0-2.5-2.5L5.5 4"/></svg></span>@CrestlineHomesQ</li>
    <li><span class="badge"><svg viewBox="0 0 12 12"><path d="M5 7l2-2M4 5.5L2.8 6.7a1.7 1.7 0 0 0 2.5 2.5L6.5 8M8 6.5l1.2-1.2a1.7 1.7 0 0 0-2.5-2.5L5.5 4"/></svg></span>@CrestlineHomesNY</li>
  </ul>
  <ul class="social social--left">
    <li><span class="badge"><svg viewBox="0 0 12 12"><path d="M5 7l2-2M4 5.5L2.8 6.7a1.7 1.7 0 0 0 2.5 2.5L6.5 8M8 6.5l1.2-1.2a1.7 1.7 0 0 0-2.5-2.5L5.5 4"/></svg></span>CrestlineHomesNY</li>
    <li><span class="badge"><svg viewBox="0 0 12 12"><path d="M5 7l2-2M4 5.5L2.8 6.7a1.7 1.7 0 0 0 2.5 2.5L6.5 8M8 6.5l1.2-1.2a1.7 1.7 0 0 0-2.5-2.5L5.5 4"/></svg></span>Info at Crestline Homes</li>
    <li><span class="badge"><svg viewBox="0 0 12 12"><path d="M5 7l2-2M4 5.5L2.8 6.7a1.7 1.7 0 0 0 2.5 2.5L6.5 8M8 6.5l1.2-1.2a1.7 1.7 0 0 0-2.5-2.5L5.5 4"/></svg></span>Crestline Homes New York</li>
  </ul>
  <div class="back-rule"></div>
  <div class="offices">
    <p class="office">418-20 Harbor Blvd<br>Bayview, NY 11590</p>
    <p class="office">72-15 Maple Ave<br>Elm Gardens, NY 11470</p>
    <p class="office">905 Union St<br>Riverton, NY 11290</p>
  </div>
</section>

<section class="card card--front" aria-label="Card front">
  <div class="brand">
    <span class="brand__mark"></span>
    <span class="brand__name">Crestline Homes</span>
  </div>
  <div class="front-rule"></div>
  <div class="person">
    <div class="person__name">DANIEL HARPER</div>
    <div class="person__title">Managing Director</div>
  </div>
  <ul class="phones">
    <li><svg class="icon" viewBox="0 0 16 16"><path d="M2 6c0-2 2-3 6-3s6 1 6 3v1h-3V5.5H5V7H2z M4 8h8l2 6H2z"/></svg>044-555 010 200</li>
    <li><svg class="icon" viewBox="0 0 16 16"><path d="M4 1h8v14H4z M5.5 3v9h5V3z"/></svg>044-555 010 200</li>
    <li><svg class="icon" viewBox="0 0 16 16"><path d="M4 1h8v4H4z M1 6h14v6h-3v3H4v-3H1z M5 10v3h6v-3z"/></svg>044-555 010 200</li>
  </ul>
  <ul class="online">
    <li>info@crestlinehomes.example<svg class="icon" viewBox="0 0 16 16"><path d="M1 3h14v10H1z"/><path d="M1 3l7 6 7-6" fill="none" stroke="#262626" stroke-width="1.5"/></svg></li>
    <li>www.mycrestlinehomes.example<svg class="icon" viewBox="0 0 16 16"><circle cx="8" cy="8" r="7"/><path d="M1 8h14M8 1c3 3 3 11 0 14M8 1c-3 3-3 11 0 14" fill="none" stroke="#262626" stroke-width="1.2"/></svg></li>
  </ul>
</section>

</body>
</html>
```